UI Redesign For Mobile Events iPhone App

We need a new UI design for our Social Events mobile app. Our app called Vessa is geared to help users find trending events in their local area. We show visual metrics on percent full and male female ratio and age group ratings. We want people to see whats going on at event before they get there through our app. Also we have a group chat portion to our app that we need included in the design. We would like to see a fresh, clean, and easy to use user interface that uses colors like, purple, blue and or hot pink.You may visit our website myvessa.example for more information about what our app is geared to do.
Updates

Target Market(s)

Our target market people that use social networks and attend social events ranging from ages 16-44.

Industry/Entity Type

Events

Requirements
Must have
• We would like to see an Example layout of all screens. (UPDATE: Please use our current background in your design, A PSD has been uploaded for you to grab the background. The Vessa Logo is NOT required to be included at the top of every screen)

-Profile Screen: Shows points earned, events attending, events created
-Event Listings Screen: Must have large image for event, visual metrics, date& time, location, attend button, invite friends button, Label for user who created the event
-Event Description Page: Shows everything as the event listing, has a description of the event, shows friends that are attending, points available
-Group Messaging Screen
-Slide Out Navigation Screen
-Notification Screen
-Ticket Screen
-Friends Activity Screen
-Friends Profile View: Shows events they've attended and points they've earned under their contact picture; invite button
-Sign-In Screen
-Register Screen

A way to label/categorize our different types of events:
-Nightlife
-Family
-Live Music & Concerts
-Restaurants
Group Chat Layout
Visual Meters for Percent Full, Male Female Ratio, Age Rating

```html
<!DOCTYPE html>
<html lang="en">
<head>
<meta charset="utf-8">
<title>Vessa – Sign Up</title>
<link href="https://fonts.googleapis.com/css2?family=Jost:wght@400;500&display=swap" rel="stylesheet">
<style>
  :root {
    --page-bg: #e9e9ec;
    --screen-bg: #05070c;
    --status-bg: #0b0d12;
    --nav-bg-top: #3a3d44;
    --nav-bg-bottom: #1d1f24;
    --text-light: #ffffff;
    --text-muted: #d7dbe2;
    --chirp-blue: #2b8fc2;
    --friend-blue: #3f5b99;
    --create-bg: #12313f;
    --create-border: #2a5566;
    --glow-blue: #2f6fa8;
    --glow-cyan: #3aa9d6;
    --glow-pink: #c0306a;
    --glow-violet: #5a3c9c;
  }
  * { box-sizing: border-box; margin: 0; padding: 0; }
  html, body {
    width: 845px; height: 1200px; overflow: hidden;
    background: var(--page-bg);
    font-family: "Jost", sans-serif;
  }
  .screen {
    position: absolute; left: 84px; top: 0;
    width: 676px; height: 1200px;
    background: var(--screen-bg);
    overflow: hidden;
    color: var(--text-light);
  }
  .status-bar {
    position: absolute; left: 0; top: 0; width: 100%; height: 42px;
    background: var(--status-bg);
    display: flex; align-items: center; justify-content: space-between;
    padding: 0 14px;
    font-size: 22px; font-weight: 500;
  }
  .status-bar .signal { display: flex; align-items: center; gap: 4px; }
  .status-bar .dot { width: 9px; height: 9px; border-radius: 50%; background: var(--text-light); }
  .status-bar .dot.empty { background: none; border: 1.5px solid var(--text-light); }
  .status-bar .carrier { margin-left: 6px; }
  .status-bar .battery { display: flex; align-items: center; gap: 8px; }
  .battery-icon { width: 44px; height: 20px; border: 2px solid var(--text-light); border-radius: 3px; padding: 2px; position: relative; }
  .battery-icon::before { content: ""; display: block; width: 100%; height: 100%; background: var(--text-light); }
  .battery-icon::after { content: ""; position: absolute; right: -6px; top: 5px; width: 3px; height: 7px; background: var(--text-light); }
  .nav-bar {
    position: absolute; left: 0; top: 42px; width: 100%; height: 92px;
    background: linear-gradient(var(--nav-bg-top), var(--nav-bg-bottom));
    border-bottom: 1px solid #000;
    display: flex; align-items: center; justify-content: space-between;
    padding: 0 18px 0 22px;
    z-index: 2;
  }
  .brand { display: flex; align-items: center; gap: 14px; font-size: 34px; font-weight: 400; letter-spacing: 2px; color: var(--text-muted); }
  .brand-mark { width: 50px; height: 50px; border-radius: 50%; background: var(--glow-violet); }
  .back-button { width: 112px; height: 54px; }
  .backdrop {
    position: absolute; left: 0; top: 134px; width: 100%; height: 1066px;
    background:
      radial-gradient(circle at 6% 8%, rgba(255,120,140,.9) 0 10px, rgba(192,48,106,.5) 30px, transparent 70px),
      radial-gradient(ellipse at 30% 22%, rgba(58,169,214,.55), transparent 42%),
      radial-gradient(ellipse at 55% 12%, rgba(192,48,106,.45), transparent 30%),
      radial-gradient(ellipse at 80% 28%, rgba(47,111,168,.6), transparent 40%),
      radial-gradient(ellipse at 45% 38%, rgba(90,60,156,.45), transparent 40%),
      linear-gradient(180deg, #10243d 0%, #0a1626 40%, var(--screen-bg) 62%);
  }
  .signup-actions {
    position: absolute; left: 83px; top: 729px; width: 505px;
    display: flex; flex-direction: column;
    z-index: 2;
  }
  .signup-button {
    height: 78px; display: flex; align-items: center; justify-content: center; gap: 18px;
    font-size: 22px; font-weight: 500; color: var(--text-light);
  }
  .signup-button .mark { width: 22px; height: 22px; border-radius: 50%; background: var(--text-light); }
  .signup-button.chirpline { background: var(--chirp-blue); }
  .signup-button.friendspace { background: var(--friend-blue); margin-top: 15px; }
  .signup-button.create-account {
    margin-top: 35px; height: 80px;
    background: var(--create-bg); border: 2px solid var(--create-border);
    font-size: 31px; font-weight: 400; letter-spacing: .5px;
  }
  .login-link {
    margin-top: 76px; text-align: center;
    font-size: 19px; color: var(--text-muted);
  }
</style>
</head>
<body>
  <main class="screen">
    <div class="status-bar">
      <div class="signal">
        <span class="dot"></span><span class="dot"></span><span class="dot"></span><span class="dot"></span><span class="dot empty"></span>
        <span class="carrier">Carrier</span>
      </div>
      <span class="clock">12:34 AM</span>
      <div class="battery"><span>100%</span><span class="battery-icon"></span></div>
    </div>

    <header class="nav-bar">
      <div class="brand"><span class="brand-mark"></span>VESSA</div>
      <svg class="back-button" viewBox="0 0 112 54" aria-label="Back">
        <path d="M20 2 H106 a4 4 0 0 1 4 4 V48 a4 4 0 0 1 -4 4 H20 L2 27 Z" fill="#2a2c31" stroke="#5a5d64" stroke-width="2"/>
        <text x="62" y="35" text-anchor="middle" fill="#ffffff" font-family="Jost, sans-serif" font-size="20">Back</text>
      </svg>
    </header>

    <div class="backdrop" role="img" aria-label="Blurred concert crowd with raised hands under blue and pink stage lights"></div>

    <section class="signup-actions">
      <a class="signup-button chirpline"><span class="mark"></span>Signup with Chirpline</a>
      <a class="signup-button friendspace"><span class="mark"></span>Signup with Friendspace</a>
      <a class="signup-button create-account">CREATE ACCOUNT</a>
      <p class="login-link">Already have account - Log in</p>
    </section>
  </main>
</body>
</html>
```